Stonebridge Building and Projects business cards

A business card with watermark background (construction work)

Company logo attached

Home improvement projects
House renovations
Bathroom and kitchen renovations
House extensions
New builds and granny flats

Director Omar Haddani
(Phone number)
omar@sbpbuilding.com.au
(Instagram logo) sbp_building

```html
<!DOCTYPE html>
<html lang="en">
<head>
<meta charset="utf-8">
<title>Stonebridge Building and Projects – Business Cards</title>
<link rel="stylesheet" href="https://fonts.googleapis.com/css2?family=Open+Sans:wght@400;600;700&display=swap">
<style>
  :root {
    --bg: #e3e3e3;
    --card-white: #f6f6f6;
    --brand-blue: #3578b5;
    --text-blue: #2f72b8;
    --ink: #3a3a3a;
    --muted: #555;
    --bullet: #333;
  }
  * { box-sizing: border-box; margin: 0; padding: 0; }
  html, body {
    width: 1200px; height: 930px; overflow: hidden;
    background: var(--bg);
    font-family: "Open Sans", Arial, sans-serif;
  }
  .card {
    position: absolute; left: 250px;
    width: 700px; height: 400px;
    box-shadow: 0 6px 18px rgba(0,0,0,.12);
  }
  .card--front { top: 45px; background: var(--card-white); }
  .card--back  { top: 485px; background: var(--brand-blue); display: flex; align-items: center; justify-content: center; }

  .holder { position: absolute; left: 48px; top: 40px; }
  .holder__name { color: var(--text-blue); font-weight: 700; font-size: 30px; line-height: 1.1; }
  .holder__role { color: var(--muted); font-size: 15px; margin-top: 2px; }

  .contacts { position: absolute; left: 48px; top: 180px; list-style: none; }
  .contacts li { display: flex; align-items: center; gap: 8px; font-size: 16px; color: var(--ink); line-height: 1.55; }
  .contacts svg { width: 16px; height: 16px; flex: none; }
  .contacts .web { color: var(--text-blue); }
  .contacts .web span { color: var(--ink); }

  .brand { position: absolute; right: 48px; top: 160px; text-align: right; }
  .brand__name { color: var(--text-blue); font-weight: 700; font-size: 24px; line-height: 1.2; }
  .brand__tagline { color: var(--text-blue); font-size: 15px; margin-top: 6px; border-top: 1.5px solid var(--text-blue); padding-top: 3px; display: inline-block; }

  .services { position: absolute; right: 48px; bottom: 34px; list-style: none; text-align: right; }
  .services li { color: var(--text-blue); font-size: 16px; line-height: 1.5; }
  .services li::after { content: ""; display: inline-block; width: 8px; height: 8px; background: var(--bullet); margin-left: 10px; vertical-align: 1px; }

  .back-brand { text-align: center; color: #fff; }
  .back-brand__name { font-weight: 700; font-size: 32px; line-height: 1.25; }
  .back-brand__tagline { font-size: 17px; margin-top: 10px; border-top: 1.5px solid #fff; padding-top: 4px; display: inline-block; }
</style>
</head>
<body>
  <section class="card card--front">
    <div class="holder">
      <h1 class="holder__name">Omar Haddani</h1>
      <p class="holder__role">Director</p>
    </div>

    <ul class="contacts">
      <li>
        <svg viewBox="0 0 16 16" aria-hidden="true"><rect x="1" y="1" width="14" height="14" rx="3" fill="#2f72b8"/></svg>
        sbp_building
      </li>
      <li>
        <svg viewBox="0 0 16 16" aria-hidden="true"><path d="M4 1.5l2.5 3-1.5 1.5a9 9 0 0 0 5 5l1.5-1.5 3 2.5-1.5 2.5C7 14 2 9 1.5 3z" fill="#2f72b8"/></svg>
        044-555 018 372
      </li>
      <li>
        <svg viewBox="0 0 16 16" aria-hidden="true"><rect x="1" y="3" width="14" height="10" fill="#2f72b8"/><path d="M1 3l7 6 7-6" fill="none" stroke="#fff" stroke-width="1.3"/></svg>
        omar@sbpbuilding.com.au
      </li>
      <li class="web">
        <svg viewBox="0 0 16 16" aria-hidden="true"><circle cx="8" cy="8" r="6.5" fill="none" stroke="#2f72b8" stroke-width="1.5"/><ellipse cx="8" cy="8" rx="3" ry="6.5" fill="none" stroke="#2f72b8" stroke-width="1.2"/><path d="M1.5 8h13M2.5 5h11M2.5 11h11" stroke="#2f72b8" stroke-width="1.1"/></svg>
        <p><span>www.</span>sbpbuilding<span>.com.au</span></p>
      </li>
    </ul>

    <div class="brand">
      <p class="brand__name">Stonebridge Building<br>and Projects</p>
      <p class="brand__tagline">Built right, built to last!</p>
    </div>

    <ul class="services">
      <li>Home improvement projects</li>
      <li>House renovations</li>
      <li>Bathroom and kitchen renovations</li>
      <li>House extensions</li>
      <li>New builds and granny flats</li>
    </ul>
  </section>

  <section class="card card--back">
    <div class="back-brand">
      <p class="back-brand__name">Stonebridge Building<br>and Projects</p>
      <p class="back-brand__tagline">Built right, built to last!</p>
    </div>
  </section>
</body>
</html>
```